Advert for Services that we offer

Brimfold Haulage Ltd need an design to represent what we do in a modern way by showing an image with a brief description and the use of corporate logo the information we will proved vie a doc file and this is to be presented in a modern way. This design will be for print & web. we have done our own design and its not great i have put this in the file repository

Target Market(s)

Motor trade

Font styles to use
Sans Serif

Colors

Designer to choose colors to be used in the design.

Requirements
Must have
• Company colour scheme as per logo within the files uploaded.
• and a small boarder to isolate it from the rest of the articles.
Nice to have
• Modern font
Should not have
• Old style font

```html
<!DOCTYPE html>
<html lang="en">
<head>
<meta charset="utf-8">
<title>Brimfold Haulage Ltd – Product Testing and Analysis</title>
<link rel="stylesheet" href="https://fonts.googleapis.com/css2?family=Bebas+Neue&family=Roboto:wght@400;500&display=swap">
<style>
  :root {
    --sky-light: #e4f7fe;
    --sky-mid: #9fe3fa;
    --sky-deep: #1cc2f0;
    --brand-blue: #1d68b3;
    --ink: #3a3f46;
    --photo-dark: #3d3f44;
    --photo-rust: #7d4634;
  }
  html, body {
    margin: 0;
    padding: 0;
    overflow: hidden;
    background: #ffffff;
  }
  .advert {
    position: relative;
    width: 1200px;
    height: 775px;
    overflow: hidden;
    background: linear-gradient(125deg, var(--sky-light) 0%, var(--sky-mid) 48%, var(--sky-deep) 100%);
    font-family: "Bebas Neue", "Arial Narrow", sans-serif;
  }
  .advert::after {
    content: "";
    position: absolute;
    inset: 0;
    border: 6px solid var(--brand-blue);
    pointer-events: none;
  }
  .service-photo {
    position: absolute;
    left: 0;
    top: 0;
    width: 240px;
    height: 775px;
    background: linear-gradient(160deg, var(--photo-dark) 0%, var(--photo-rust) 100%);
  }
  .brand {
    position: absolute;
    left: 262px;
    top: 128px;
    width: 236px;
    text-align: center;
    color: var(--brand-blue);
  }
  .brand-mark {
    display: block;
    width: 52px;
    height: 52px;
    margin: 0 auto 10px;
    background: var(--brand-blue);
  }
  .brand-name {
    font-size: 30px;
    line-height: 1;
    letter-spacing: 1px;
  }
  .divider {
    position: absolute;
    left: 541px;
    top: 104px;
    width: 1px;
    height: 137px;
    background: var(--brand-blue);
  }
  .headline {
    position: absolute;
    left: 588px;
    top: 96px;
    margin: 0;
    font-weight: 400;
    font-size: 80px;
    line-height: 75px;
    letter-spacing: 1px;
    color: var(--brand-blue);
  }
  .service-list {
    position: absolute;
    left: 600px;
    top: 271px;
    margin: 0;
    padding: 0;
    list-style: none;
  }
  .service-list li {
    position: relative;
    padding-left: 26px;
    font-size: 41px;
    line-height: 54.5px;
    letter-spacing: 1.5px;
    color: var(--ink);
  }
  .service-list li::before {
    content: "";
    position: absolute;
    left: 2px;
    top: 25px;
    width: 6px;
    height: 6px;
    border-radius: 50%;
    background: var(--ink);
  }
  .contact-bar {
    position: absolute;
    left: 588px;
    top: 591px;
    width: 522px;
    height: 50px;
    box-sizing: border-box;
    border: 1.5px solid var(--brand-blue);
    border-radius: 25px;
    display: flex;
    align-items: center;
    font-family: "Roboto", Arial, sans-serif;
    font-size: 19px;
    color: var(--brand-blue);
  }
  .contact-web {
    width: 310px;
    text-align: center;
  }
  .contact-sep {
    width: 1px;
    height: 22px;
    background: var(--brand-blue);
  }
  .contact-phone {
    flex: 1;
    text-align: center;
  }
</style>
</head>
<body>
<main class="advert">
  <div class="service-photo" role="img" aria-label="Photo of a technician measuring the bore of a flanged housing with a digital dial gauge"></div>

  <div class="brand">
    <span class="brand-mark"></span>
    <div class="brand-name">Brimfold Haulage Ltd</div>
  </div>

  <div class="divider"></div>

  <h1 class="headline">Product Testing<br>and Analysis</h1>

  <ul class="service-list">
    <li>Metallurgical Testing</li>
    <li>Bearing Pre-Load Testing</li>
    <li>Bore Measurement</li>
    <li>New Product Evaluation</li>
    <li>Product Analysis &amp; Report</li>
  </ul>

  <div class="contact-bar">
    <span class="contact-web">www.brimfold-haulage.co.uk</span>
    <span class="contact-sep"></span>
    <span class="contact-phone">0161 496 0732</span>
  </div>
</main>
</body>
</html>
```